Awesome new bottle needs Awesome new label

We need an awesome label design for our new bottle. It is a square bottle with 4 flat surfaces for the label. These surfaces make it easier to play with transparent labels.
The water comes from the Mount Talvey Springs. Themes that we want to concentrate on are purity of the water as well as the clarity of the bottle. Think Tesmar's new label design for inspiration. I am looking for something like that. I have attached pictures of the bottle as well as the schematics of the label.
The brand to be used is "Vireli", which means Solar in French. I would like transparent labels as the smooth surfaces make good areas to play with this idea.
Thanks and good luck!
Kal
Reason: Waiting for the final designs from my shortlisted designers

```html
<!DOCTYPE html>
<html lang="en">
<head>
<meta charset="utf-8">
<title>Vireli Natural Mineral Water – Label Layout</title>
<link href="https://fonts.googleapis.com/css2?family=Arimo:wght@400;700&family=Roboto+Condensed:wght@400&family=Nunito:wght@900&display=swap" rel="stylesheet">
<style>
  :root{
    --sky:#0aaeeb;
    --deep:#1b6ad6;
    --navy:#1f2f9c;
    --ink:#2f3b45;
    --line:#3a4a55;
    --sun:#f7d23e;
    --white:#ffffff;
    --table-head:#4a86e8;
    --row-a:#d6e2f6;
    --row-b:#e9eff9;
    --dim:#444;
  }
  *{box-sizing:border-box;margin:0;padding:0}
  html,body{width:1200px;height:1000px;overflow:hidden;background:var(--white)}
  body{position:relative;font-family:"Arimo",Arial,sans-serif;color:var(--ink)}
  .abs{position:absolute}

  /* label strip */
  .strip{left:53px;top:204px;width:1120px;height:211px;background:var(--sky)}
  .divider{position:absolute;top:0;width:1px;height:100%;background:var(--line)}
  .glue-tab{position:absolute;left:0;top:0;width:48px;height:100%;display:flex;align-items:center;justify-content:center}
  .glue-tab span{transform:rotate(-90deg);font-size:16px;white-space:nowrap;color:var(--ink)}

  .origin{position:absolute;left:69px;top:26px;line-height:17px;font-size:15px;color:var(--ink)}
  .origin .small{font-size:12px}
  .origin b{font-weight:700}
  .origin .gap{height:18px}

  .analysis{position:absolute;left:374px;top:10px;width:132px;border-collapse:collapse;font-size:7.5px;background:var(--white);border:2px solid var(--white)}
  .analysis th{background:var(--table-head);color:var(--white);text-align:left;padding:3px 4px;font-weight:700;height:16px}
  .analysis td{padding:2px 4px;height:17px;border-top:1px solid var(--white);vertical-align:top}
  .analysis td:first-child{width:64px;border-right:1px solid var(--white)}
  .analysis tr:nth-child(odd) td{background:var(--row-a)}
  .analysis tr:nth-child(even) td{background:var(--row-b)}
  .analysis tr.tall td{height:24px;line-height:8px}

  .front{position:absolute;left:584px;top:0;width:268px;height:100%}
  .glow{position:absolute;left:18px;top:28px;width:232px;height:128px;border-radius:50%;
        background:radial-gradient(ellipse at center,#fff 55%,rgba(255,255,255,.6) 75%,rgba(255,255,255,0) 100%)}
  .brand{display:flex;align-items:center;justify-content:center;gap:8px;font-family:"Nunito",sans-serif;font-weight:900;color:var(--navy)}
  .brand i{display:block;border-radius:50%;background:var(--sun)}
  .front .brand{position:absolute;left:0;right:0;top:72px;font-size:40px}
  .front .brand i{width:22px;height:22px}
  .tagline{position:absolute;left:0;right:0;text-align:center;color:var(--white);font-size:16px}
  .front .tagline{top:186px}

  .facts{position:absolute;left:909px;top:38px;width:170px;background:var(--white);border:2px solid var(--line);font-family:"Roboto Condensed",sans-serif;font-size:16px;color:#222}
  .facts div{display:flex;justify-content:space-between;padding:0 12px;height:27.5px;align-items:center;border-top:2px solid var(--line)}
  .facts div:first-child{border-top:0;justify-content:center}

  /* dimensions */
  .dim-text{position:absolute;font-size:12px;color:var(--dim);background:var(--white);padding:0 4px}

  /* options */
  .option{width:268px;height:211px;overflow:hidden}
  .option .brand{position:absolute;left:0;right:0;font-size:38px}
  .option .brand i{width:20px;height:20px}
  .opt1{left:160px;top:596px;background:var(--sky)}
  .opt1 .brand{top:76px}
  .opt1 .tagline{top:145px;color:var(--ink)}
  .opt2{left:466px;top:596px;background:radial-gradient(circle at 50% 58%,#fff 0,#fff 32%,#bcd6f5 48%,var(--deep) 68%)}
  .opt2 .brand{top:104px}
  .opt3{left:772px;top:596px;background:linear-gradient(#ffffff 0%,#bfe7f8 45%,#7fcdf1 100%)}
  .opt3 .splash{position:absolute;left:0;bottom:0;width:100%;height:68px;background:linear-gradient(#59b7ea,#0f6fc4)}
  .opt3 .brand{top:104px}
  .opt3 .tagline{top:187px}
  .opt-name{position:absolute;font-size:15px;color:#333}
</style>
</head>
<body>

<!-- label strip -->
<div class="abs strip">
  <div class="glue-tab"><span>glue tab</span></div>
  <div class="divider" style="left:48px"></div>
  <div class="divider" style="left:316px"></div>
  <div class="divider" style="left:584px"></div>
  <div class="divider" style="left:852px"></div>

  <div class="origin">
    <p class="small">Sourced and Bottled at</p>
    <p><b>The Talvey Mountain Springs,</b></p>
    <p>Indonesia.</p>
    <div class="gap"></div>
    <p class="small">Manufactured for and imported by:</p>
    <p><b>Norvale Trading Pte Ltd,</b></p>
    <p>42 Harbour Lane Road,</p>
    <p>Singapore 041562.</p>
    <p>TEL: +6560001234</p>
  </div>

  <table class="analysis">
    <tr><th>TypicalAnalysis</th><th>(mg/L)</th></tr>
    <tr><td>Bicarbonate</td><td>103.0</td></tr>
    <tr><td>Calcium</td><td>8.9</td></tr>
    <tr><td>Sodium</td><td>18.0</td></tr>
    <tr><td>Chlorides</td><td>&lt;3.2</td></tr>
    <tr><td>Suphates</td><td>11.1</td></tr>
    <tr><td>Magnesium</td><td>10.0</td></tr>
    <tr><td>Potassium</td><td>1.60</td></tr>
    <tr><td>pH at Source</td><td>7.72</td></tr>
    <tr class="tall"><td>Total Dissolved Solids at 180&deg;C</td><td>144</td></tr>
  </table>

  <div class="front">
    <div class="glow"></div>
    <div class="brand"><i></i>Vireli</div>
    <p class="tagline">Natural Mineral Water</p>
  </div>

  <div class="facts">
    <div>Nutritional Facts</div>
    <div><span>Energy</span><span>0kcal</span></div>
    <div><span>Protein</span><span>0g</span></div>
    <div><span>Total Fat</span><span>0g</span></div>
    <div><span>Carbohydrates</span><span>0g</span></div>
  </div>
</div>

<!-- dimension lines -->
<svg class="abs" style="left:0;top:0" width="1200" height="470" aria-hidden="true">
  <defs>
    <marker id="arrow" viewBox="0 0 10 10" refX="10" refY="5" markerWidth="7" markerHeight="7" orient="auto-start-reverse">
      <path d="M0 1 L10 5 L0 9 z" fill="#444"/>
    </marker>
  </defs>
  <g stroke="#444" stroke-width="1" fill="none">
    <line x1="28" y1="204" x2="50" y2="204"/>
    <line x1="28" y1="415" x2="50" y2="415"/>
    <line x1="38" y1="206" x2="38" y2="413" marker-start="url(#arrow)" marker-end="url(#arrow)"/>
    <line x1="53" y1="418" x2="53" y2="438"/>
    <line x1="101" y1="418" x2="101" y2="456"/>
    <line x1="369" y1="418" x2="369" y2="440"/>
    <line x1="1173" y1="418" x2="1173" y2="456"/>
    <line x1="55" y1="430" x2="99" y2="430" marker-start="url(#arrow)" marker-end="url(#arrow)"/>
    <line x1="103" y1="430" x2="367" y2="430" marker-start="url(#arrow)" marker-end="url(#arrow)"/>
    <line x1="103" y1="448" x2="1171" y2="448" marker-start="url(#arrow)" marker-end="url(#arrow)"/>
  </g>
  <text x="42" y="310" transform="rotate(-90 42 310)" font-family="Arimo, sans-serif" font-size="13" fill="#444" text-anchor="middle" dy="-8">45 mm</text>
</svg>
<span class="dim-text" style="left:58px;top:436px;font-size:11px">10 mm</span>
<span class="dim-text" style="left:204px;top:423px">57 mm</span>
<span class="dim-text" style="left:596px;top:440px">228 mm</span>

<!-- front panel options -->
<div class="abs option opt1">
  <div class="brand"><i></i>Vireli</div>
  <p class="tagline">Natural Mineral Water</p>
</div>
<span class="opt-name" style="left:164px;top:810px">opt1</span>

<div class="abs option opt2">
  <div class="brand"><i></i>Vireli</div>
</div>
<span class="opt-name" style="left:474px;top:810px">opt2</span>

<div class="abs option opt3">
  <div class="splash" role="img" aria-label="Splash of clear blue water across the base of the label"></div>
  <div class="brand"><i></i>Vireli</div>
  <p class="tagline">Natural Mineral Water</p>
</div>
<span class="opt-name" style="left:779px;top:810px">opt3</span>

</body>
</html>
```